Software allocation system needs a business card design

We need a business card designed for our software platform - www.tallivo.com.au

At the moment the logo and website is all black and white, we are happy for suggestions on implementing some colour throughout either the logo or business card.

Industry/Entity Type

Software

Font styles to use
Sans Serif

Colors

Designer to choose colors to be used in the design.

```html
<!DOCTYPE html>
<html lang="en">
<head>
<meta charset="utf-8">
<title>Tallivo business card</title>
<link rel="stylesheet" href="https://fonts.googleapis.com/css2?family=Exo+2:wght@300;400;600&display=swap">
<style>
  :root {
    --backdrop: #e8e5e0;
    --card-white: #ffffff;
    --card-dark: #2c2c2d;
    --card-grey: #6f6f72;
    --text-light: #ffffff;
    --text-dark: #2c2c2d;
  }
  * { box-sizing: border-box; margin: 0; padding: 0; }
  html, body {
    width: 1200px; height: 672px; overflow: hidden;
    background: var(--backdrop);
    font-family: "Exo 2", sans-serif;
  }
  .canvas {
    position: relative; width: 1200px; height: 672px;
    display: flex; align-items: center; justify-content: center;
  }
  .card {
    position: relative; width: 350px; height: 610px;
    background: var(--card-white);
    box-shadow: 0 10px 30px rgba(0,0,0,0.18);
    overflow: hidden;
  }
  .card-shapes { position: absolute; inset: 0; width: 100%; height: 100%; }
  .brand {
    position: absolute; top: 92px; right: 34px;
    display: flex; align-items: center; gap: 10px;
  }
  .brand-dot {
    width: 20px; height: 20px; border-radius: 50%;
    background: var(--text-dark);
  }
  .brand-name {
    font-weight: 300; font-size: 34px; letter-spacing: 6px;
    color: var(--text-dark);
  }
  .identity {
    position: absolute; top: 282px; left: 26px;
    color: var(--text-light); text-transform: uppercase;
  }
  .identity-name { font-weight: 600; font-size: 21px; letter-spacing: 1px; }
  .identity-role { font-weight: 400; font-size: 13px; letter-spacing: 1px; margin-top: 2px; }
  .contact {
    position: absolute; top: 372px; right: 26px;
    color: var(--text-light); text-align: right;
    font-size: 14px; letter-spacing: 1px; line-height: 1.35;
  }
  .contact-address { margin-bottom: 22px; }
  .contact-row {
    display: flex; align-items: center; justify-content: flex-end;
    gap: 8px; margin-bottom: 8px; white-space: nowrap;
  }
  .contact-icon { width: 14px; height: 14px; flex: none; fill: none; stroke: var(--text-light); stroke-width: 1.6; }
</style>
</head>
<body>
<main class="canvas">
  <article class="card">
    <svg class="card-shapes" viewBox="0 0 350 610" preserveAspectRatio="none" aria-hidden="true">
      <polygon points="0,200 140,200 350,190 350,250 0,270" fill="var(--card-dark)"/>
      <polygon points="0,270 350,220 350,300 0,350" fill="var(--card-grey)"/>
      <polygon points="0,350 350,300 350,610 0,610" fill="var(--card-dark)"/>
    </svg>

    <div class="brand">
      <span class="brand-dot"></span>
      <span class="brand-name">TALLIVO</span>
    </div>

    <div class="identity">
      <div class="identity-name">Daniel Forsythe</div>
      <div class="identity-role">Financial Advisor</div>
    </div>

    <div class="contact">
      <p class="contact-address">027 9th floor,Arden<br>Harbour Road NSW</p>
      <p class="contact-row">021 468 3570
        <svg class="contact-icon" viewBox="0 0 16 16"><path d="M4 2 L6 2 L7 5 L5.5 6.5 Q7 9.5 9.5 10.5 L11 9 L14 10 L14 12 Q13 14 11 14 Q3 12 2 4 Q2 2 4 2 Z"/></svg>
      </p>
      <p class="contact-row">021 468 3570
        <svg class="contact-icon" viewBox="0 0 16 16"><rect x="4.5" y="1.5" width="7" height="13" rx="1"/><line x1="7" y1="12" x2="9" y2="12"/></svg>
      </p>
      <p class="contact-row">hello@tallivo.com.au
        <svg class="contact-icon" viewBox="0 0 16 16"><rect x="1.5" y="3.5" width="13" height="9"/><polyline points="1.5,3.5 8,9 14.5,3.5"/></svg>
      </p>
      <p class="contact-row">www.tallivo.com.au
        <svg class="contact-icon" viewBox="0 0 16 16"><circle cx="8" cy="8" r="6.5"/><ellipse cx="8" cy="8" rx="3" ry="6.5"/><line x1="1.5" y1="8" x2="14.5" y2="8"/></svg>
      </p>
    </div>
  </article>
</main>
</body>
</html>
```